Poster for a online company that buys your stuff

SwapKestrel offers a website which customers can get a instant offer for stuff their looking to sell. They then Courier the items in to us and they get paid the same day it arrives
We're looking for an eye catching design which portrays our hassle free process
We'll need your help to come up with a slogan/catch phrase and our easy 1,2,3 process so customers can see the poster and instantly have a clear understanding of what we do
1. Get an instant offer on our website
2. Send your item(s) to us
3.Get paid within 24 Hours
Industry/Entity Type
It Company
Look and feel
Each slider illustrates characteristics of the customer's brand and the style your logo design should communicate.

```html
<!DOCTYPE html>
<html lang="en">
<head>
<meta charset="utf-8">
<title>SwapKestrel – How It Works Banners</title>
<link rel="stylesheet" href="https://fonts.googleapis.com/css2?family=Bebas+Neue&family=Lobster&family=Roboto:wght@500;700&display=swap">
<style>
  :root {
    --sheet-bg: #210e10;
    --title-grey: #8a8585;
    --leaf-green: #9ccb3b;
    --ink: #111111;
    --caption-dark: #3c4a1e;
    --white: #ffffff;
  }
  * { margin: 0; padding: 0; box-sizing: border-box; }
  html, body { width: 1200px; height: 1200px; overflow: hidden; }
  body {
    background: var(--sheet-bg);
    font-family: "Roboto", Arial, sans-serif;
    position: relative;
  }
  .sheet-title {
    position: absolute; top: 38px; left: 0; width: 1200px;
    text-align: center; color: var(--title-grey);
    font-size: 44px; font-weight: 500; letter-spacing: 1px;
  }
  .banner {
    position: absolute; width: 566px; height: 285px;
    background: var(--leaf-green); overflow: hidden;
  }
  .banner--a { left: 13px; top: 181px; }
  .banner--b { left: 611px; top: 181px; }
  .banner--c { left: 13px; top: 517px; }
  .banner--d { left: 611px; top: 517px; }
  .banner--e { left: 315px; top: 845px; }

  .banner__head {
    height: 51px; background: var(--white);
    display: flex; align-items: center; justify-content: center; gap: 10px;
    color: var(--ink);
  }
  .banner--e .banner__head { background: transparent; color: var(--white); }
  .headline--caps { font-family: "Bebas Neue", Impact, sans-serif; font-size: 38px; line-height: 1; padding-top: 4px; }
  .headline--script { font-family: "Lobster", cursive; font-size: 28px; line-height: 1; }
  .banner--e .headline--script { text-decoration: underline; text-decoration-thickness: 2px; text-underline-offset: 4px; }

  .brand { display: flex; align-items: center; gap: 3px; align-self: flex-end; margin-bottom: 6px; }
  .brand__dot { width: 8px; height: 8px; border-radius: 50%; background: var(--leaf-green); }
  .banner--e .brand__dot { background: var(--white); }
  .brand__name { font-size: 8px; font-weight: 700; color: var(--ink); }
  .banner--e .brand__name { color: var(--white); }

  .step { position: absolute; top: 65px; width: 190px; text-align: center; }
  .step--1 { left: 6px; }
  .step--2 { left: 186px; }
  .step--3 { left: 380px; }
  .step__pill {
    display: inline-block; background: var(--white); color: var(--ink);
    font-size: 16px; font-weight: 500; line-height: 27px;
    height: 27px; padding: 0 16px; border-radius: 14px;
  }
  .step__badge {
    width: 116px; height: 116px; margin: 9px auto 0;
    border: 3px solid var(--white); border-radius: 50%;
    display: flex; align-items: center; justify-content: center;
    color: var(--ink);
  }
  .banner--b .step__badge, .banner--d .step__badge { color: var(--white); }
  .step__badge svg { width: 76px; height: 76px; }
  .step__caption {
    margin-top: 12px; font-size: 16px; font-weight: 500; line-height: 20px;
    color: var(--caption-dark);
  }
  .banner--c .step__caption { color: var(--white); }
</style>
</head>
<body>

<svg width="0" height="0" style="position:absolute" aria-hidden="true">
  <defs>
    <symbol id="icon-laptop" viewBox="0 0 100 100">
      <path fill="currentColor" d="M14 36h38v8H22v28h50V58h8v22H14z"/>
      <path fill="currentColor" d="M4 82h92l-6 8H10z"/>
      <rect fill="currentColor" x="62" y="14" width="12" height="12"/>
      <rect fill="currentColor" x="76" y="6" width="12" height="12"/>
      <rect fill="currentColor" x="52" y="28" width="10" height="10"/>
      <rect fill="currentColor" x="64" y="30" width="10" height="10"/>
      <rect fill="currentColor" x="76" y="22" width="10" height="10"/>
      <rect fill="currentColor" x="44" y="44" width="8" height="8"/>
      <rect fill="currentColor" x="56" y="42" width="8" height="8"/>
      <rect fill="currentColor" x="68" y="44" width="8" height="8"/>
      <rect fill="currentColor" x="36" y="56" width="6" height="6"/>
      <rect fill="currentColor" x="48" y="56" width="6" height="6"/>
      <rect fill="currentColor" x="60" y="56" width="6" height="6"/>
    </symbol>
    <symbol id="icon-cart" viewBox="0 0 100 100">
      <path fill="none" stroke="currentColor" stroke-width="7" stroke-linejoin="round" stroke-linecap="round" d="M8 16h14l12 46h40"/>
      <path fill="currentColor" d="M24 28h40a20 20 0 0 0 16 18l-4 14H34z"/>
      <circle fill="currentColor" cx="38" cy="78" r="8"/>
      <circle fill="currentColor" cx="68" cy="78" r="8"/>
      <circle fill="currentColor" cx="78" cy="24" r="17"/>
      <path fill="none" stroke="var(--leaf-green)" stroke-width="5" stroke-linecap="round" stroke-linejoin="round" d="M70 24l6 6 10-12"/>
    </symbol>
    <symbol id="icon-desk" viewBox="0 0 100 100">
      <circle fill="currentColor" cx="30" cy="18" r="9"/>
      <path fill="currentColor" d="M20 30h18l10 16h14v8H44l-4-6v14H30l6 30h-8l-6-26V30z"/>
      <path fill="currentColor" d="M8 40h6v34h18v18h-6V80H14v12H8z"/>
      <rect fill="currentColor" x="44" y="54" width="50" height="6"/>
      <rect fill="currentColor" x="60" y="60" width="30" height="32"/>
      <path fill="currentColor" d="M74 20l16-4 4 30-18 6z"/>
      <rect fill="currentColor" x="58" y="10" width="16" height="10" transform="rotate(-20 66 15)"/>
      <rect fill="currentColor" x="76" y="4" width="14" height="9" transform="rotate(15 83 8)"/>
    </symbol>
  </defs>
</svg>

<h1 class="sheet-title">SUBMISSION IDEAS - 02</h1>

<!-- Banner A -->
<section class="banner banner--a">
  <header class="banner__head"><span class="headline--caps">HOW IT WORKS?</span><span class="brand"><span class="brand__dot"></span><span class="brand__name">SwapKestrel</span></span></header>
  <div class="step step--1"><span class="step__pill">Step 01</span><div class="step__badge"><svg><use href="#icon-laptop"/></svg></div><p class="step__caption">Get an instant offer<br>on our website</p></div>
  <div class="step step--2"><span class="step__pill">Step 02</span><div class="step__badge"><svg><use href="#icon-cart"/></svg></div><p class="step__caption">Send your item(s)<br>to us</p></div>
  <div class="step step--3"><span class="step__pill">Step 03</span><div class="step__badge"><svg><use href="#icon-desk"/></svg></div><p class="step__caption">Get paid within<br>24 Hours</p></div>
</section>

<!-- Banner B -->
<section class="banner banner--b">
  <header class="banner__head"><span class="headline--caps">HOW IT WORKS?</span><span class="brand"><span class="brand__dot"></span><span class="brand__name">SwapKestrel</span></span></header>
  <div class="step step--1"><span class="step__pill">Step 01</span><div class="step__badge"><svg><use href="#icon-laptop"/></svg></div><p class="step__caption">Get an instant offer<br>on our website</p></div>
  <div class="step step--2"><span class="step__pill">Step 02</span><div class="step__badge"><svg><use href="#icon-cart"/></svg></div><p class="step__caption">Send your item(s)<br>to us</p></div>
  <div class="step step--3"><span class="step__pill">Step 03</span><div class="step__badge"><svg><use href="#icon-desk"/></svg></div><p class="step__caption">Get paid within<br>24 Hours</p></div>
</section>

<!-- Banner C -->
<section class="banner banner--c">
  <header class="banner__head"><span class="headline--caps">HOW IT WORKS?</span><span class="brand"><span class="brand__dot"></span><span class="brand__name">SwapKestrel</span></span></header>
  <div class="step step--1"><span class="step__pill">Step 01</span><div class="step__badge"><svg><use href="#icon-laptop"/></svg></div><p class="step__caption">Get an instant offer<br>on our website</p></div>
  <div class="step step--2"><span class="step__pill">Step 02</span><div class="step__badge"><svg><use href="#icon-cart"/></svg></div><p class="step__caption">Send your item(s)<br>to us</p></div>
  <div class="step step--3"><span class="step__pill">Step 03</span><div class="step__badge"><svg><use href="#icon-desk"/></svg></div><p class="step__caption">Get paid within<br>24 Hours</p></div>
</section>

<!-- Banner D -->
<section class="banner banner--d">
  <header class="banner__head"><span class="headline--script">Sell &amp; Get Paid Within 24 Hours</span><span class="brand"><span class="brand__dot"></span><span class="brand__name">SwapKestrel</span></span></header>
  <div class="step step--1"><span class="step__pill">Step 01</span><div class="step__badge"><svg><use href="#icon-desk"/></svg></div><p class="step__caption">Get an instant offer<br>on our website</p></div>
  <div class="step step--2"><span class="step__pill">Step 02</span><div class="step__badge"><svg><use href="#icon-cart"/></svg></div><p class="step__caption">Send your item(s)<br>to us</p></div>
  <div class="step step--3"><span class="step__pill">Step 03</span><div class="step__badge"><svg><use href="#icon-desk"/></svg></div><p class="step__caption">Get paid within<br>24 Hours</p></div>
</section>

<!-- Banner E -->
<section class="banner banner--e">
  <header class="banner__head"><span class="headline--script">Sell &amp; Get Paid Within 24 Hours</span><span class="brand"><span class="brand__dot"></span><span class="brand__name">SwapKestrel</span></span></header>
  <div class="step step--1"><span class="step__pill">Step 01</span><div class="step__badge"><svg><use href="#icon-laptop"/></svg></div><p class="step__caption">Get an instant offer<br>on our website</p></div>
  <div class="step step--2"><span class="step__pill">Step 02</span><div class="step__badge"><svg><use href="#icon-cart"/></svg></div><p class="step__caption">Send your item(s)<br>to us</p></div>
  <div class="step step--3"><span class="step__pill">Step 03</span><div class="step__badge"><svg><use href="#icon-desk"/></svg></div><p class="step__caption">Get paid within<br>24 Hours</p></div>
</section>

</body>
</html>
```